Business Identity Stationary

Already have the logo which is in the attached files so only need the Business STationary
1) Double Sided Business Card
2) Letterhead
3) Presentation folder with business card holder on inside cover
4) WIth compliments slip
See information for business cards, letterhead and presentation folder below.

This should be a simply job using a logo we already had designed along with a little device. I suggest using the device off center and perhaps lower in the corner in an abstract way. Also the logo device could be used as a watermark for the letterhead. The designer who created the logo presented something that I think works well for a business card. The front of the double sided business card could have the name logo small for the website address and only use the Lime device on the front. Then on the back could be the name Barrow Advisory logo.

Please note that for the business card the black and lime green background do look good. Also please think of using the lime device separately in an unusual way.

It has been brought to my attention that.my budget was far to low. Hopefully this.will attract you to the project. 

The parent company of Barrow Advisory is TallHeron holdings. I have uploaded a file of the Tall Heron business card I really like. Perhaps use this business card as a guide to the type of modern and clean style I am looking for. It also works to have the Barrow Advisroy and Tall Heron similar.

Reason: Still haven't received anything exactly right.

Industry/Entity Type

Business

Font styles to use
Sans Serif

Colors
9bcb3c
000000
5c5c5c
add136
cadf82
eaf2cf
f9fbf2
1b1b1b
757575

Requirements
Must have
• 1) Double Sided Business Card
Marta Kellendorf
Director
Tel: +505 8264 3170
Email: mk@barrowadvisory-example.com
Website: www.barrowadvisory-example.com

Frederick Kellendorf
Director
Tel: +505 8264 3172
Email: fk@barrowadvisory-example.com

Lucia Brenes Otaduy
Director
Tel: 8642 1093
Email: lbo@barrowadvisory-example.com

2) Letterhead
Logo
Lime Logo Device
Website Address: www.barrowadvisory-example.com
Small print on bottom: Barrow Advisory a Tall Heron Holding Company SA. RUC J0487000239518

3) Presentation Folder
Traditional Presentation folder with inside front cover spot for the insertion of business card.

4) With Compliments slip

```html
<!DOCTYPE html>
<html lang="en">
<head>
<meta charset="utf-8">
<title>Barrow Advisory – Business Card</title>
<link href="https://fonts.googleapis.com/css2?family=Open+Sans:wght@300;400;600&display=swap" rel="stylesheet">
<style>
  :root {
    --lime: #86c440;
    --lime-dark: #74b033;
    --ink: #1b1b1b;
    --white: #ffffff;
    --paper: #f9fbf2;
    --stage: #ececea;
  }
  * { box-sizing: border-box; margin: 0; padding: 0; }
  html, body {
    width: 1200px; height: 1024px; overflow: hidden;
    background: var(--stage);
    font-family: "Open Sans", Arial, sans-serif;
  }
  .card {
    position: absolute;
    left: 240px;
    width: 720px; height: 410px;
    overflow: hidden;
    box-shadow: 0 6px 18px rgba(0,0,0,.12);
  }
  /* front */
  .card--front { top: 62px; background: var(--white); }
  .wordmark {
    position: absolute;
    display: flex; align-items: center; gap: 14px;
    font-weight: 300; letter-spacing: 1px; white-space: nowrap;
  }
  .card--front .wordmark { left: 44px; top: 100px; font-size: 48px; color: var(--ink); }
  .wordmark__dot { width: 18px; height: 18px; border-radius: 50%; background: var(--lime); flex: none; }
  .contact-band {
    position: absolute; left: 262px; top: 232px;
    width: 458px; height: 178px;
    background: var(--lime);
    color: var(--white);
    padding: 26px 0 0 22px;
  }
  .contact__name { font-size: 17px; font-weight: 600; }
  .contact__role { font-weight: 400; }
  .contact__sep { display: inline-block; width: 2px; height: 16px; background: var(--white); margin: 0 8px; vertical-align: -2px; }
  .contact__list { list-style: none; margin-top: 10px; font-size: 14px; line-height: 24px; }
  .contact__list li { display: flex; align-items: center; gap: 9px; }
  .contact__list svg { width: 13px; height: 13px; flex: none; }
  /* back */
  .card--back { top: 548px; background: var(--lime); }
  .card--back .wordmark { left: 286px; top: 150px; font-size: 50px; color: var(--white); }
  .back__rule { position: absolute; left: 30px; top: 258px; width: 270px; height: 1.5px; background: var(--white); }
  .back__web { position: absolute; left: 36px; top: 270px; font-size: 14px; color: var(--white); }
</style>
</head>
<body>

<section class="card card--front" aria-label="Business card front">
  <div class="wordmark"><span class="wordmark__dot"></span>Barrow Advisory</div>
  <div class="contact-band">
    <p class="contact__name">Marta Kellendorf<span class="contact__sep"></span><span class="contact__role">Director</span></p>
    <ul class="contact__list">
      <li>
        <svg viewBox="0 0 16 16" aria-hidden="true"><path fill="#fff" d="M3.6 1.2l2.3 2.6-1.2 1.7c.9 2 2.4 3.6 4.4 4.6l1.7-1.2 2.6 2.3-1.4 2.4C7 13.4 2.6 9 1.2 2.6z"/></svg>
        +505 8264 3170
      </li>
      <li>
        <svg viewBox="0 0 16 16" aria-hidden="true"><rect x="1" y="3" width="14" height="10" fill="#fff"/><path d="M1.5 3.5L8 9l6.5-5.5" fill="none" stroke="#86c440" stroke-width="1.4"/></svg>
        mk@barrowadvisory-example.com
      </li>
      <li>
        <svg viewBox="0 0 16 16" aria-hidden="true"><circle cx="8" cy="8" r="6.5" fill="none" stroke="#fff" stroke-width="1.4"/><ellipse cx="8" cy="8" rx="2.8" ry="6.5" fill="none" stroke="#fff" stroke-width="1.2"/><path d="M1.5 8h13" stroke="#fff" stroke-width="1.2"/></svg>
        www.barrowadvisory-example.com
      </li>
    </ul>
  </div>
</section>

<section class="card card--back" aria-label="Business card back">
  <div class="wordmark"><span class="wordmark__dot" style="background:#fff"></span>Barrow Advisory</div>
  <div class="back__rule"></div>
  <p class="back__web">www.barrowadvisory-example.com</p>
</section>

</body>
</html>
```